Biz Card

MARKETING today is the most rapidly changing business discipline. Media options to reach customers, actual customer preferences and consumer buying decisions change by the minute . . . no, by the second. The behavioral data generated by all aspects of the business and the new technologies that put the data to work together produce the potential to generate business intelligence and guide smart resource allocation to influence purchase and retention. However, to realize this potential, marketing professionals at all levels and in all organizations must continuously improve their skills not just from on-the-job training but by learning from masters in the field. The Bright Horizon Guild is the training center that serves this professional development need.model logos:msi.orgama.orgcontentmarketinginstitute.comBook covers on MarketingMetrics, Marketing Anaytics
Industry/Entity Type
Business
Contact Information for Business Card
Roy A. YoungCEOMarketing Science Academyphone: 310-601-4755email: roy@marketingscience.comAddress:437 South Rexford DriveBeverly Hills, CA 89377
Look and feel
Each slider illustrates characteristics of the customer's brand and the style your logo design should communicate.

```html
<!DOCTYPE html>
<html lang="en">
<head>
<meta charset="utf-8">
<title>Bright Horizon Guild – Business Card</title>
<link rel="stylesheet" href="https://fonts.googleapis.com/css2?family=Questrial&family=Roboto:wght@400;700&display=swap">
<style>
  :root {
    --backdrop: #e9e9ea;
    --card: #ffffff;
    --brand-blue: #3c6b9f;
    --brand-gray: #555558;
    --text-gray: #4a4a4d;
  }
  html, body {
    margin: 0;
    padding: 0;
    width: 1200px;
    height: 1200px;
    overflow: hidden;
    background: var(--backdrop);
  }
  .canvas {
    position: relative;
    width: 1200px;
    height: 1200px;
  }
  .card {
    position: absolute;
    width: 713px;
    height: 418px;
    background: var(--card);
    overflow: hidden;
  }
  .card--front { left: 238px; top: 119px; }
  .card--back  { left: 230px; top: 644px; }
  .card__band {
    position: absolute;
    left: 0;
    bottom: 0;
    width: 100%;
    height: 16px;
    background: var(--brand-blue);
  }
  .brand {
    position: absolute;
    display: flex;
    align-items: center;
  }
  .brand__square {
    background: var(--brand-blue);
    flex: none;
  }
  .brand__name {
    font-family: "Questrial", sans-serif;
    color: var(--brand-gray);
    margin: 0;
    font-weight: 400;
  }
  .card--front .brand { left: 162px; top: 152px; gap: 26px; }
  .card--front .brand__square { width: 88px; height: 88px; }
  .card--front .brand__name { font-size: 35px; line-height: 36px; }

  .card--back .brand { left: 62px; top: 170px; gap: 20px; }
  .card--back .brand__square { width: 62px; height: 62px; }
  .card--back .brand__name { font-size: 25px; line-height: 25px; }

  .contact {
    position: absolute;
    left: 404px;
    top: 100px;
    font-family: "Roboto", sans-serif;
    color: var(--text-gray);
  }
  .contact__name {
    margin: 0;
    font-size: 26px;
    font-weight: 700;
    color: var(--brand-blue);
    letter-spacing: -0.3px;
  }
  .contact__title {
    margin: 8px 0 0;
    font-size: 15px;
    letter-spacing: 0.5px;
  }
  .contact__address {
    margin: 30px 0 0;
    font-size: 17px;
    line-height: 24px;
    font-style: normal;
  }
  .contact__list {
    list-style: none;
    margin: 6px 0 0;
    padding: 0;
    font-size: 17px;
    line-height: 24px;
  }
  .contact__list li {
    display: flex;
    align-items: center;
  }
  .contact__icon {
    width: 16px;
    height: 16px;
    margin: 0 20px 0 2px;
    fill: var(--brand-blue);
    flex: none;
  }
</style>
</head>
<body>
<main class="canvas">
  <section class="card card--front" aria-label="Card front">
    <div class="brand">
      <span class="brand__square"></span>
      <h1 class="brand__name">Bright<br>Horizon<br>Guild</h1>
    </div>
    <div class="card__band"></div>
  </section>

  <section class="card card--back" aria-label="Card back">
    <div class="brand">
      <span class="brand__square"></span>
      <p class="brand__name">Bright<br>Horizon<br>Guild</p>
    </div>
    <div class="contact">
      <h2 class="contact__name">Neil P. Barton</h2>
      <p class="contact__title">CEO</p>
      <address class="contact__address">912 North Calloway Lane<br>Beverly Hills, CA 89377</address>
      <ul class="contact__list">
        <li>
          <svg class="contact__icon" viewBox="0 0 16 16" aria-hidden="true">
            <path d="M1 5c0-2 3-3 7-3s7 1 7 3v1h-4V4.5H5V6H1z"/>
            <path d="M4 7h8l2 7H2z"/>
          </svg>
          310-555-0182
        </li>
        <li>
          <svg class="contact__icon" viewBox="0 0 16 16" aria-hidden="true">
            <path d="M1 3h14v10H1z M2.5 4.5v1l5.5 4 5.5-4v-1L8 8.5z" fill-rule="evenodd"/>
          </svg>
          neil@brighthorizonguild.com
        </li>
        <li>
          <svg class="contact__icon" viewBox="0 0 16 16" aria-hidden="true">
            <path fill="none" stroke="#3c6b9f" stroke-width="1.4" d="M8 1.5a6.5 6.5 0 1 0 0 13a6.5 6.5 0 1 0 0-13zM1.5 8h13M8 1.5c-3 3.5-3 9.5 0 13M8 1.5c3 3.5 3 9.5 0 13M2.8 4.8h10.4M2.8 11.2h10.4"/>
          </svg>
          www.brighthorizonguild.com
        </li>
      </ul>
    </div>
    <div class="card__band"></div>
  </section>
</main>
</body>
</html>
```